Business Card for a Dental Office

The design should communicate integrity, quality and reliability. We also want the card look elegant, simple, but still stand out, different from the traditional-dental-office business card.

Industry/Entity Type

Business

```html
<!DOCTYPE html>
<html lang="en">
<head>
<meta charset="utf-8">
<title>Harlow Dental Studio – Business Card</title>
<link rel="stylesheet" href="https://fonts.googleapis.com/css2?family=Oswald:wght@500;700&family=Open+Sans:wght@400;600&display=swap">
<style>
  :root {
    --stage: #e7e4df;
    --paper: #ffffff;
    --ink: #111111;
    --gold: #c3b22e;
    --gold-deep: #9c8d1c;
    --soft-white: #f4f4f4;
  }
  html, body {
    margin: 0;
    width: 1200px;
    height: 1022px;
    overflow: hidden;
    background: var(--stage);
  }
  .card {
    position: absolute;
    left: 150px;
    top: 254px;
    width: 900px;
    height: 514px;
    background: var(--paper);
    border-radius: 14px;
    overflow: hidden;
    box-shadow: 0 14px 40px rgba(0,0,0,0.22);
  }
  .card-bands {
    position: absolute;
    inset: 0;
  }
  .brand {
    position: absolute;
    left: 56px;
    top: 96px;
    display: flex;
    align-items: center;
    gap: 22px;
  }
  .brand-square {
    width: 72px;
    height: 72px;
    background: var(--ink);
  }
  .brand-name {
    font-family: "Oswald", sans-serif;
    font-weight: 700;
    font-size: 60px;
    line-height: 1;
    color: var(--ink);
    letter-spacing: 0.5px;
    text-transform: uppercase;
  }
  .tagline {
    position: absolute;
    left: 150px;
    top: 180px;
    font-family: "Open Sans", sans-serif;
    font-weight: 600;
    font-size: 19px;
    letter-spacing: 2px;
    text-transform: uppercase;
    color: var(--gold-deep);
  }
  .tagline .accent { color: var(--gold); }
  .person {
    position: absolute;
    right: 32px;
    top: 224px;
    text-align: right;
  }
  .person-name {
    font-family: "Oswald", sans-serif;
    font-weight: 700;
    font-size: 38px;
    line-height: 1;
    color: var(--ink);
    text-transform: uppercase;
  }
  .person-role {
    margin-top: 6px;
    font-family: "Open Sans", sans-serif;
    font-size: 15px;
    letter-spacing: 2px;
    color: var(--soft-white);
    text-transform: uppercase;
  }
  .contacts {
    position: absolute;
    left: 34px;
    top: 396px;
    margin: 0;
    padding: 0;
    list-style: none;
  }
  .contacts li {
    display: flex;
    align-items: center;
    gap: 14px;
    height: 32px;
    font-family: "Open Sans", sans-serif;
    font-size: 22px;
    color: var(--gold);
    letter-spacing: 0.5px;
  }
  .contact-icon { width: 18px; height: 18px; flex: none; }
</style>
</head>
<body>
  <div class="card">
    <svg class="card-bands" width="900" height="514" viewBox="0 0 900 514" aria-hidden="true">
      <polyline points="0,350 520,350 584,294" fill="none" stroke="var(--gold)" stroke-width="3"/>
      <polygon points="0,366 530,366 596,304 900,304 900,514 0,514" fill="var(--ink)"/>
      <polygon points="610,212 900,212 900,294 584,294" fill="var(--gold)"/>
    </svg>

    <div class="brand">
      <div class="brand-square"></div>
      <div class="brand-name">Harlow Dental Studio</div>
    </div>
    <div class="tagline">Honest care for <span class="accent">every single smile</span></div>

    <div class="person">
      <div class="person-name">Mara Ellison</div>
      <div class="person-role">Director</div>
    </div>

    <ul class="contacts">
      <li>
        <svg class="contact-icon" viewBox="0 0 24 24" aria-hidden="true"><path d="M6.6 10.8a15 15 0 0 0 6.6 6.6l2.2-2.2a1 1 0 0 1 1-.25 11.4 11.4 0 0 0 3.6.57 1 1 0 0 1 1 1V20a1 1 0 0 1-1 1A17 17 0 0 1 3 4a1 1 0 0 1 1-1h3.5a1 1 0 0 1 1 1c0 1.25.2 2.45.57 3.57a1 1 0 0 1-.25 1z" fill="#fff"/></svg>
        +41 5873-2916
      </li>
      <li>
        <svg class="contact-icon" viewBox="0 0 24 24" aria-hidden="true"><rect x="2" y="5" width="20" height="14" fill="none" stroke="#fff" stroke-width="2"/><polyline points="2,5 12,13 22,5" fill="none" stroke="#fff" stroke-width="2"/></svg>
        info@harlowdentalstudio.com
      </li>
      <li>
        <svg class="contact-icon" viewBox="0 0 24 24" aria-hidden="true"><circle cx="12" cy="12" r="9" fill="none" stroke="#fff" stroke-width="2"/><ellipse cx="12" cy="12" rx="4" ry="9" fill="none" stroke="#fff" stroke-width="1.5"/><line x1="3" y1="12" x2="21" y2="12" stroke="#fff" stroke-width="1.5"/></svg>
        www.harlowdentalstudio.com
      </li>
    </ul>
  </div>
</body>
</html>
```